Vardem Web, LLC. is the name of the company that will be an Internet startup working in E-commerce and

We are a new company and going to start the business by hiring people we need. We are on “Hiring Now…” status right now which we like to be displayed on the website homepage.
The website should allow us to start the hiring process with letting people see and apply for jobs posted on the website.

the company logo is attached.

Target Market(s)

Tech Job Seekers, Programmers, iOS and Android Developers, Software engineers, Graphic designers, QA engineers, Customer Service Reps,...

Industry/Entity Type

Internet

Number of Pages Required

5+ page

Font styles to use
Serif
Sans Serif

Colors

Designer to choose colors to be used in the design.

Requirements
Must have
• We need a system to help job seekers to upload the resume and cover letter and fill the required forms and answer some questions on a form designed to evaluate the job seekers and let them know if they fit in the position and should apply for it.
• We also want job seekers to do a Pre-Employment Tests including Aptitude, Personality, and Skills after they qualified for a job which links our website to web-based pre-employment testing services websites like (Talvexa, Plivmark, Quorvane & Associates, Dunholt Assessment, …)

```html
<!DOCTYPE html>
<html lang="en">
<head>
<meta charset="utf-8">
<title>Vardem Web — Hiring Now</title>
<link href="https://fonts.googleapis.com/css2?family=Poppins:wght@400;500;600&family=Open+Sans:wght@400;600&display=swap" rel="stylesheet">
<style>
:root{
  --orange:#f05a1e;
  --blue:#1f7fc4;
  --blue-mid:#2a8fd0;
  --teal:#4cb7c6;
  --ink:#2b2b2b;
  --text:#555;
  --muted:#888;
  --line:#e3e3e3;
  --light:#f4f4f4;
}
*{box-sizing:border-box;margin:0;padding:0}
html,body{width:1200px;height:3340px;overflow:hidden;background:#fff}
body{font-family:"Open Sans",Arial,sans-serif;color:var(--text);position:relative}
.abs{position:absolute}
h1,h2,h3,h4,.nav a,.brand{font-family:"Poppins",Arial,sans-serif}

/* header */
.brand{left:98px;top:40px;display:flex;align-items:center;gap:12px;font-weight:600;font-size:38px;line-height:1;color:var(--blue);letter-spacing:.5px;white-space:nowrap}
.brand .dot{width:18px;height:18px;background:var(--orange)}
.contact-top{right:98px;top:24px;display:flex;gap:34px;font-size:16px;color:#444}
.contact-top span{display:flex;align-items:center;gap:10px}
.nav{right:98px;top:76px;display:flex;gap:8px}
.nav a{font-size:14px;font-weight:500;color:#333;text-decoration:none;padding:6px 13px;letter-spacing:.5px}
.nav a.active{border:1px solid var(--blue);color:var(--blue);border-radius:2px}

/* hero */
.hero{left:0;top:125px;width:1200px;height:600px;background:linear-gradient(180deg,#c9c2b8 0%,#8f8577 55%,#5d544b 100%)}
.hero-title{left:0;top:385px;width:1200px;text-align:center;color:#fff;font-size:62px;font-weight:600;letter-spacing:1px}
.hero-arrow{top:385px;width:30px;height:30px;border-radius:50%;background:rgba(0,0,0,.45)}
.search-strip{left:0;top:640px;width:1200px;height:85px;background:rgba(40,40,40,.88)}
.field{top:663px;height:38px;background:#fff;border-radius:2px;font-size:12px;color:#999;padding:0 12px;display:flex;align-items:center;gap:8px}
.search-btn{left:876px;top:663px;width:130px;height:38px;background:var(--blue-mid);color:#fff;font-family:"Poppins",sans-serif;font-size:14px;font-weight:600;display:flex;align-items:center;justify-content:center;gap:10px}

/* welcome */
.welcome-title{left:0;top:790px;width:1200px;text-align:center;font-size:40px;font-weight:500;color:var(--ink)}
.welcome-title b{color:var(--blue);font-weight:500}
.welcome-text{left:160px;top:860px;width:880px;text-align:center;font-size:12px;line-height:22px;color:#444}
.tile{top:962px;height:163px;color:#fff;display:flex;flex-direction:column;align-items:center;justify-content:flex-end;padding-bottom:24px;gap:22px;font-family:"Poppins",sans-serif;font-size:15px;font-weight:500}
.tile .ico{width:62px;height:62px;border-radius:50%;background:#fff;display:flex;align-items:center;justify-content:center}

/* jobs */
.section-h{font-size:24px;font-weight:500;color:var(--ink);letter-spacing:.5px}
.job-box{left:98px;top:1240px;width:667px;height:345px;border:1px solid var(--line);border-top:3px solid #d7e6f3;padding:14px}
.job{height:100px;border:1px solid var(--line);margin-bottom:12px;display:flex;align-items:center;padding:0 18px;gap:18px;position:relative}
.job .thumb{width:62px;height:54px;background:linear-gradient(135deg,#6c7a88,#cfd6dc)}
.job h4{font-size:14px;font-weight:400;color:#333;margin-bottom:10px}
.job .meta{display:flex;gap:28px;font-size:11px;color:var(--muted)}
.job .more{position:absolute;right:18px;top:34px;background:var(--blue-mid);color:#fff;font-size:12px;padding:8px 14px;border-radius:2px}
.talent{left:798px;top:1245px;width:304px;height:340px;border:1px solid var(--line)}
.talent .img{height:180px;background:linear-gradient(135deg,#5a6f86,#b6c2cc 60%,#e6e9ec)}
.talent .meta{padding:20px 16px 12px;font-size:11px;color:var(--muted);display:flex;gap:26px}
.talent p{padding:0 16px;font-size:12px;line-height:20px;color:#666}

/* career band */
.career{left:0;top:1680px;width:1200px;height:465px;background:linear-gradient(90deg,#ececec 0%,#e2e2e2 50%,#d2d0cc 100%)}
.career-title{left:98px;top:1778px;font-size:34px;font-weight:500;line-height:48px;color:var(--ink);letter-spacing:.5px}
.career-text{left:98px;top:1885px;width:500px;font-size:12px;line-height:22px;color:#444}
.pet-btn{left:98px;top:1992px;padding:10px 20px;background:var(--blue);color:#fff;font-size:14px;font-family:"Poppins",sans-serif;font-weight:500}

/* blog */
.blog-title{left:0;top:2215px;width:1200px;text-align:center;font-size:34px;font-weight:500;color:var(--ink)}
.post{top:2305px;width:310px}
.post .img{height:180px;position:relative;overflow:hidden}
.post .date{position:absolute;left:0;bottom:0;width:70px;height:70px;background:var(--blue);clip-path:polygon(0 0,100% 100%,0 100%)}
.post .date span{position:absolute;left:10px;bottom:8px;color:#fff;font-size:12px;line-height:16px;font-weight:600}
.post h4{font-size:16px;font-weight:400;color:#333;margin:20px 0 10px}
.post p{font-size:12px;line-height:20px;color:#555}

/* testimonial */
.quote-band{left:0;top:2683px;width:1200px;height:307px;background:linear-gradient(90deg,#e65a1c,#ee6320 60%,#d8531a)}
.quote-mark{left:0;top:2705px;width:1200px;text-align:center;color:#fff;font-family:"Poppins",sans-serif;font-size:120px;font-weight:600;line-height:120px}
.quote-text{left:210px;top:2810px;width:780px;text-align:center;color:#fff;font-size:12px;line-height:22px}
.quote-name{left:0;top:2900px;width:1200px;text-align:center;color:#fff;font-size:14px}
.dots{left:552px;top:2945px;display:flex;gap:8px}
.dots i{width:28px;height:3px;background:rgba(255,255,255,.5)}
.dots i:first-child{background:#fff}

/* footer */
.footer{left:0;top:2990px;width:1200px;height:290px;background:var(--light)}
.f-brand{left:98px;top:3078px;font-size:28px;gap:10px}
.f-brand .dot{width:14px;height:14px}
.socials{left:132px;top:3160px;display:flex;gap:8px}
.socials i{width:22px;height:22px;border:1px solid #777;border-radius:50%}
.f-col h4{font-size:17px;font-weight:500;color:var(--ink);letter-spacing:.5px;margin-bottom:20px}
.f-col{top:3045px;font-size:12px;color:#444;line-height:18px}
.f-row{display:flex;gap:14px;margin-bottom:16px}
.email-in{width:245px;height:40px;background:#fff;border:1px solid #e6e6e6;margin:16px 0 14px;padding:0 10px;display:flex;align-items:center;font-size:11px;color:#888}
.sub-btn{display:inline-block;background:var(--orange);color:#fff;font-weight:600;font-size:12px;padding:10px 14px}
.links li{list-style:none;font-size:11px;line-height:22px;padding-left:16px;position:relative}
.links li::before{content:"›";position:absolute;left:2px;color:#666}
.copy{left:0;top:3280px;width:1200px;height:60px;border-top:1px solid #ddd;text-align:center;line-height:60px;font-size:11px;color:#666}
</style>
</head>
<body>

<header>
  <div class="abs brand"><span>Vardem Web</span><span class="dot"></span></div>
  <div class="abs contact-top">
    <span><svg width="24" height="24" viewBox="0 0 24 24"><circle cx="12" cy="12" r="11" fill="none" stroke="#1f7fc4" stroke-width="1.5"/><path d="M8 7l2 0 1 3-1.5 1a6 6 0 0 0 3.5 3.5l1-1.5 3 1v2a1 1 0 0 1-1 1A9 9 0 0 1 7 8a1 1 0 0 1 1-1z" fill="#1f7fc4"/></svg>+1 00 555 017 284</span>
    <span><svg width="24" height="24" viewBox="0 0 24 24"><circle cx="12" cy="12" r="11" fill="none" stroke="#1f7fc4" stroke-width="1.5"/><rect x="6.5" y="8" width="11" height="8" fill="none" stroke="#1f7fc4" stroke-width="1.4"/><path d="M6.5 8l5.5 4.5L17.5 8" fill="none" stroke="#1f7fc4" stroke-width="1.4"/></svg>info@vardemweb.com</span>
  </div>
  <nav class="abs nav">
    <a class="active">HOME</a><a>FIND A JOB</a><a>OUR SERVICES</a><a>ABOUT US</a><a>BLOG</a><a>CONTACT US</a>
  </nav>
</header>

<section>
  <div class="abs hero" role="img" aria-label="Team of young professionals in a meeting around an office table"></div>
  <div class="abs hero-arrow" style="left:40px"><svg width="30" height="30" viewBox="0 0 30 30"><path d="M17 10l-5 5 5 5" fill="none" stroke="#fff" stroke-width="2"/></svg></div>
  <div class="abs hero-arrow" style="left:1130px"><svg width="30" height="30" viewBox="0 0 30 30"><path d="M13 10l5 5-5 5" fill="none" stroke="#fff" stroke-width="2"/></svg></div>
  <h1 class="abs hero-title">HIRING NOW...</h1>
  <div class="abs search-strip"></div>
  <div class="abs field" style="left:188px;width:216px">I am looking for...</div>
  <div class="abs field" style="left:418px;width:216px"><svg width="10" height="12" viewBox="0 0 10 12"><path d="M5 0a4 4 0 0 1 4 4c0 3-4 8-4 8S1 7 1 4a4 4 0 0 1 4-4z" fill="#888"/></svg>Jobseeker</div>
  <div class="abs field" style="left:648px;width:214px;justify-content:space-between">Job Title (Select)<svg width="8" height="12" viewBox="0 0 8 12"><path d="M1 4l3-3 3 3M1 8l3 3 3-3" fill="none" stroke="#666"/></svg></div>
  <div class="abs search-btn">SEARCH <svg width="16" height="16" viewBox="0 0 16 16"><circle cx="6.5" cy="6.5" r="5" fill="none" stroke="#fff" stroke-width="2"/><path d="M10 10l5 5" stroke="#fff" stroke-width="2"/></svg></div>
</section>

<section>
  <h2 class="abs welcome-title">WELCOME TO <b>VARDEM</b></h2>
  <p class="abs welcome-text">Lorem ipsum dolor sit amet, consectetur adipiscing elit, sed do eiusmod tempor incididunt ut labore et dolore magna aliqua. Ut enim ad minim veniam, quis nostrud exercitation ullamco laboris nisi ut aliquip ex ea commodo consequat. Duis aute irure dolor in reprehenderit in voluptate velit esse cillum dolore eu fugiat nulla pariatur. Excepteur sint occaecat cupidatat non proident, sunt in culpa qui officia deserunt mollit anim id est laborum</p>

  <div class="abs tile" style="left:98px;width:245px;background:var(--orange)">
    <span class="ico"><svg width="30" height="30" viewBox="0 0 30 30"><path d="M15 4v14M9 10l6-6 6 6" fill="none" stroke="#f05a1e" stroke-width="3"/><rect x="4" y="20" width="22" height="6" fill="#f05a1e"/></svg></span>UPLOAD THE RESUME</div>
  <div class="abs tile" style="left:353px;width:244px;background:var(--blue-mid)">
    <span class="ico"><svg width="30" height="30" viewBox="0 0 30 30"><path d="M8 3h10l5 5v19H8z" fill="#2a8fd0"/><path d="M11 13h9M11 17h9M11 21h9" stroke="#fff" stroke-width="1.6"/></svg></span>COVER LETTER</div>
  <div class="abs tile" style="left:604px;width:244px;background:var(--teal)">
    <span class="ico"><svg width="30" height="30" viewBox="0 0 30 30"><rect x="5" y="6" width="18" height="20" fill="none" stroke="#4cb7c6" stroke-width="2.4"/><path d="M12 19l2-5 11-11 3 3-11 11z" fill="#4cb7c6"/></svg></span>FILL THE REQUIRED FORMS</div>
  <div class="abs tile" style="left:857px;width:245px;background:var(--blue)">
    <span class="ico"><svg width="32" height="30" viewBox="0 0 32 30"><circle cx="16" cy="10" r="5" fill="#1f7fc4"/><path d="M8 25a8 8 0 0 1 16 0z" fill="#1f7fc4"/><circle cx="7" cy="12" r="3.5" fill="#1f7fc4"/><circle cx="25" cy="12" r="3.5" fill="#1f7fc4"/><path d="M1 24a6 6 0 0 1 8-5.5M31 24a6 6 0 0 0-8-5.5" fill="#1f7fc4"/></svg></span>JOB SEEKERS</div>
</section>

<section>
  <h3 class="abs section-h" style="left:98px;top:1188px">FIND A JOB</h3>
  <div class="abs job-box">
    <div class="job"><div class="thumb" role="img" aria-label="Person working at a desk"></div><div><h4>Marketing Coordinator - SEO / SEM Experience FULL-TIME</h4><div class="meta"><span>▦ Company Name</span><span>⌖ 12 Elm Row Brixford</span><span>▤ Jan 10, 2017</span></div></div><span class="more">View More</span></div>
    <div class="job"><div class="thumb" role="img" aria-label="Laptop on a desk"></div><div><h4>Marketing Coordinator - SEO / SEM Experience FULL-TIME</h4><div class="meta"><span>▦ Company Name</span><span>⌖ 12 Elm Row Brixford</span><span>▤ Jan 10, 2017</span></div></div><span class="more">View More</span></div>
    <div class="job"><div class="thumb" role="img" aria-label="Professional in an office"></div><div><h4>Marketing Coordinator - SEO / SEM Experience FULL-TIME</h4><div class="meta"><span>▦ Company Name</span><span>⌖ 12 Elm Row Brixford</span><span>▤ Jan 10, 2017</span></div></div><span class="more">View More</span></div>
  </div>

  <h3 class="abs section-h" style="left:798px;top:1188px">FIND TALENT</h3>
  <div class="abs talent">
    <div class="img" role="img" aria-label="Hands reviewing documents with a pen"></div>
    <div class="meta"><span>⌖ 12 Elm Row Brixford</span><span>▤ Jan 10, 2017</span></div>
    <p>Lorem ipsum dolor sit amet, consectetur adipiscing elit, sed do eiusmod tempor incididunt ut labore et dolore magna aliqua. Ut enim ad minim veniam, quis nostrud exercitation</p>
  </div>
</section>

<section>
  <div class="abs career" role="img" aria-label="Young man with a laptop relaxing on a yellow bean bag"></div>
  <h2 class="abs career-title">BUILDING CAREER,<br>LEADING TO SUCCESS</h2>
  <p class="abs career-text">Nemo enim ipsam voluptatem quia voluptas sit aspernatur aut odit aut fugit, sed quia consequuntur magni dolores eos qui ratione voluptatem sequi nesciunt. Neque porro quisquam est, qui dolorem ipsum quia dolor sit amet, consectetur, adipisci velit, sed quia non numquam eius modi tempora incidunt ut labore et</p>
  <div class="abs pet-btn">Pre-Employment Tests</div>
</section>

<section>
  <h2 class="abs blog-title">LATEST BLOG</h2>
  <article class="abs post" style="left:98px">
    <div class="img" role="img" aria-label="Business people shaking hands" style="background:linear-gradient(135deg,#9aa4ad,#e2e6ea)"><div class="date"><span>SEP<br>09</span></div></div>
    <h4>Nemo enim ipsam voluptatem quia</h4>
    <p>Sed ut perspiciatis unde omnis iste natus error sit uptatem accusantium doloremque laudantium, totam rem aperiam, eaque ipsa quae ab illo inventore veritatis</p>
  </article>
  <article class="abs post" style="left:445px">
    <div class="img" role="img" aria-label="Woman sitting on the floor with a laptop" style="background:linear-gradient(135deg,#dfe8ef,#b9cbd8)"><div class="date"><span>SEP<br>09</span></div></div>
    <h4>Nemo enim ipsam voluptatem quia</h4>
    <p>Sed ut perspiciatis unde omnis iste natus error sit uptatem accusantium doloremque laudantium, totam rem aperiam, eaque ipsa quae ab illo inventore veritatis</p>
  </article>
  <article class="abs post" style="left:792px">
    <div class="img" role="img" aria-label="Business team meeting in an office" style="background:linear-gradient(135deg,#7b6e64,#c9beb4)"><div class="date"><span>SEP<br>09</span></div></div>
    <h4>Nemo enim ipsam voluptatem quia</h4>
    <p>Sed ut perspiciatis unde omnis iste natus error sit uptatem accusantium doloremque laudantium, totam rem aperiam, eaque ipsa quae ab illo inventore veritatis</p>
  </article>
</section>

<section>
  <div class="abs quote-band"></div>
  <div class="abs quote-mark">”</div>
  <p class="abs quote-text">"Sed ut perspiciatis unde omnis iste natus error sit voluptatem accusantium doloremque laudantium, totam rem aperiam, eaque ipsa quae ab illo inventore veritatis et quasi architecto beatae vitae dicta sunt explicabo. Nemo enim ipsam voluptatem quia voluptas sit aspernatur aut odit aut fugit, sed quia consequuntur magni dolores eos qui ratione</p>
  <p class="abs quote-name">- Corwin Halloway, Vardem</p>
  <div class="abs dots"><i></i><i></i><i></i></div>
</section>

<footer>
  <div class="abs footer"></div>
  <div class="abs brand f-brand"><span>Vardem Web</span><span class="dot"></span></div>
  <div class="abs socials"><i></i><i></i><i></i><i></i></div>

  <div class="abs f-col" style="left:336px">
    <h4>CONTACT US</h4>
    <div class="f-row"><svg width="12" height="16" viewBox="0 0 10 12"><path d="M5 0a4 4 0 0 1 4 4c0 3-4 8-4 8S1 7 1 4a4 4 0 0 1 4-4z" fill="#444"/></svg><span>2180 Harlow Ave, Suite 300<br>Fenmore CA 90411</span></div>
    <div class="f-row"><svg width="12" height="14" viewBox="0 0 24 24"><path d="M5 2l4 0 2 6-3 2a12 12 0 0 0 6 6l2-3 6 2v4a2 2 0 0 1-2 2A19 19 0 0 1 3 4a2 2 0 0 1 2-2z" fill="#444"/></svg><span>Phone: (310) 555-0192</span></div>
    <div class="f-row"><svg width="14" height="12" viewBox="0 0 14 10"><rect width="14" height="10" fill="#444"/><path d="M0 0l7 5 7-5" fill="none" stroke="#fff"/></svg><span>Email: info@vardemweb.com</span></div>
  </div>

  <div class="abs f-col" style="left:634px;width:260px">
    <h4>SIGN UP FOR NEWSLETTER</h4>
    <p style="font-size:11px">Excepteur sint occaecat cupidatat non proident, sunt in culpa qui officia deserunt</p>
    <div class="email-in">Enter email</div>
    <span class="sub-btn">SUBSCRIPTION</span>
  </div>

  <div class="abs f-col" style="left:980px">
    <h4>QUICK LINKS</h4>
    <ul class="links"><li>Home</li><li>About Us</li><li>Our Services</li><li>Training and HR</li><li>Blog</li><li>Faqs</li><li>Contact Us</li></ul>
  </div>

  <div class="abs copy">©2017 Vardem, All Rights Reserved.</div>
</footer>

</body>
</html>
```